NZ First of it's kind solutions directory and marketplace for busy Mums needs a business card design

We need a business card design for our new nationwide business in NZ (long term plans to go global). We provide solutions to the everyday challenges that busy Mums face by connecting them with quality communities and suppliers of carefully selected, relevant products and services. We sell direct via our online marketplace. The final design should communicate our values of inclusivity, quality and smart solutions. Colours should incorporate our logo colour palette of #477077 and #6ba8b2. Our website is at https://www.brightnestmums.example

Target Market(s)

busy Mums, Age 28 – 50, female, income over $100K, location main centres NZ primarily but NZ wide. Is likely juggling work or career with a young family. Probably had hobbies which have fallen by the wayside.
-Wants to succeed in her chosen career without compromising on family life
-to successfully juggle her career without feeling like she is compromising her children
- Is time poor, something always has to give and it’s generally her health (she’ll stay up late, get stressed)
- probably ex corporate or professional career. Has discretional income

Industry/Entity Type

Business

Contact Information for Business Card

Lena Forbisher, Founder, BrightNestMums.example (Strapline Tap; Gather; Sorted), 47 Kowhai Terrace, Ellerslie, Auckland 1051, New Zealand. Mob: 021 483 517 Ph: +64 (0)9 571 4860

Font styles to use
Other font styles liked:
• Raleway, and/or Architects Daughter

Colors
00a990
33b8a4
86cfc6
cfeae6

Requirements
Must have
• the above details, streamline. the logo and colours associated with those logos
Should not have
• foil or metallic colours

```html
<!DOCTYPE html>
<html lang="en">
<head>
<meta charset="utf-8">
<title>BrightNestMums – Business Card</title>
<link rel="stylesheet" href="https://fonts.googleapis.com/css2?family=Roboto+Condensed:ital,wght@0,400;1,400&family=Varela+Round&display=swap">
<style>
  :root {
    --brand-deep: #477077;
    --brand-light: #6ba8b2;
    --brand-dark: #3b5c63;
    --ink: #3a3f42;
    --icon: #4a6e75;
    --card: #fbfbfb;
    --backdrop: #e8e8e8;
    --card-edge: #d8d8d8;
  }
  * { box-sizing: border-box; margin: 0; padding: 0; }
  html, body { width: 1200px; height: 576px; overflow: hidden; }
  body {
    background: var(--backdrop);
    position: relative;
    font-family: "Roboto Condensed", "Arial Narrow", sans-serif;
    color: var(--ink);
  }
  .card {
    position: absolute;
    top: 138px;
    width: 484px;
    height: 294px;
    background: var(--card);
    border: 1px solid var(--card-edge);
    border-radius: 14px;
    overflow: hidden;
  }
  .card--front { left: 82px; }
  .card--back { left: 600px; }

  /* Front */
  .brand {
    position: absolute;
    left: 34px;
    top: 124px;
    display: flex;
    align-items: center;
    gap: 12px;
  }
  .brand__dot {
    width: 28px;
    height: 28px;
    border-radius: 50%;
    background: var(--brand-deep);
    flex: none;
  }
  .brand__name {
    font-family: "Varela Round", sans-serif;
    font-size: 27px;
    line-height: 1;
    color: var(--brand-deep);
  }
  .strapline {
    position: absolute;
    left: 76px;
    top: 158px;
    font-size: 9.5px;
    letter-spacing: 2.6px;
    color: var(--ink);
    text-transform: uppercase;
    white-space: nowrap;
  }
  .strapline__sep { color: var(--brand-light); margin: 0 5px; }
  .front-art {
    position: absolute;
    left: 300px;
    top: 22px;
    width: 184px;
    height: 272px;
    background: linear-gradient(160deg, var(--brand-light) 0%, var(--brand-deep) 45%, var(--brand-dark) 100%);
  }

  /* Back */
  .identity {
    position: absolute;
    right: 264px;
    top: 112px;
    text-align: right;
  }
  .identity__name {
    font-family: "Varela Round", sans-serif;
    font-size: 18px;
    line-height: 22px;
    color: var(--brand-deep);
  }
  .identity__role {
    font-style: italic;
    font-size: 12px;
    line-height: 16px;
    margin-bottom: 4px;
  }
  .identity__address {
    font-size: 12.5px;
    line-height: 18px;
    font-style: normal;
  }
  .contacts {
    position: absolute;
    left: 248px;
    top: 114px;
    list-style: none;
  }
  .contacts__item {
    display: flex;
    align-items: center;
    gap: 8px;
    font-size: 12.5px;
    line-height: 18.4px;
    white-space: nowrap;
  }
  .contacts__icon {
    width: 10px;
    height: 10px;
    fill: var(--icon);
    flex: none;
  }
</style>
</head>
<body>

  <section class="card card--front" aria-label="Card front">
    <div class="brand">
      <span class="brand__dot"></span>
      <span class="brand__name">BrightNestMums</span>
    </div>
    <p class="strapline">Tap<span class="strapline__sep">|</span>Gather<span class="strapline__sep">|</span>Sorted</p>
    <div class="front-art" role="img" aria-label="Large brand decoration in deep and light teal"></div>
  </section>

  <section class="card card--back" aria-label="Card back">
    <div class="identity">
      <h1 class="identity__name">Lena Forbisher</h1>
      <p class="identity__role">Founder</p>
      <address class="identity__address">47 Kowhai Terrace, Ellerslie,<br>Auckland 1051, New Zealand</address>
    </div>
    <ul class="contacts">
      <li class="contacts__item">
        <svg class="contacts__icon" viewBox="0 0 10 10" aria-hidden="true"><path d="M2.5 0h5a1 1 0 0 1 1 1v8a1 1 0 0 1-1 1h-5a1 1 0 0 1-1-1V1a1 1 0 0 1 1-1zM3 1.2v6.3h4V1.2zM5 8.2a.55.55 0 1 0 0 1.1.55.55 0 0 0 0-1.1z"/></svg>
        021 483 517
      </li>
      <li class="contacts__item">
        <svg class="contacts__icon" viewBox="0 0 10 10" aria-hidden="true"><path d="M0 3.2C0 1.6 2.3.8 5 .8s5 .8 5 2.4V4H7.3V2.9H2.7V4H0zM2.8 4.4h4.4L9 7v2.2H1V7zM5 5.6a1.3 1.3 0 1 0 0 2.6 1.3 1.3 0 0 0 0-2.6z"/></svg>
        +64 (0)9 571 4860
      </li>
      <li class="contacts__item">
        <svg class="contacts__icon" viewBox="0 0 10 10" aria-hidden="true"><path d="M0 2h10v.6L5 5.8 0 2.6zM0 3.6l5 3.2 5-3.2V8.4H0z"/></svg>
        www.BrightNestMums.example
      </li>
      <li class="contacts__item">
        <svg class="contacts__icon" viewBox="0 0 10 10" aria-hidden="true"><path d="M5 0a5 5 0 1 0 0 10A5 5 0 0 0 5 0zm0 1c.7 0 1.4 1.2 1.6 3H3.4C3.6 2.2 4.3 1 5 1zM1.1 4h1.3c0-.9.2-1.8.5-2.5A4 4 0 0 0 1.1 4zm6.5 0h1.3a4 4 0 0 0-1.8-2.5c.3.7.5 1.6.5 2.5zM1.1 6a4 4 0 0 0 1.8 2.5c-.3-.7-.5-1.6-.5-2.5zm2.3 0c.2 1.8.9 3 1.6 3s1.4-1.2 1.6-3zm4.2 0c0 .9-.2 1.8-.5 2.5A4 4 0 0 0 8.9 6z"/></svg>
        lena@brightnestmums.example
      </li>
    </ul>
  </section>

</body>
</html>
```